Lotstallmart.com Webpage Design

Design Brief for lotstallmart.com (Copy of Brief also in attached Word file)

Name of Website- lotstallmart.com (existing logo and look & feel of website to be changed)

Logo - Finalised. The logo files are attached with the brief as “logo.jpeg”. The “Blue- Grey” version of the logo is for use on lighter backgrounds and the “Orange-White” version of the logo is for use on darker backgrounds. (A full Black version of the logo is also attached). Both versions may be used in different parts of the website. All attached files are in .png format.
Status - The website in functional and is undergoing user trials. However, we want to improve the look & feel of the website so at it seems
a. cotemporary,
b. Easy to Navigate
c. professional and
d. Vibrant.

Please visit ‘lotstallmart.com’ to check out the website and its functionalities – please use it only as a reference for the features & functions to be provided, however the designer should use a ‘Free Hand’ in designing the composition of various parts of the webpage without getting too influenced by the existing design

Objective of the Website ‘lotstallmart.com –
a. It is a portal focussed on listing of ‘Retail’ specific real-estate properties by developers, owners and realty brokers. The properties shall listed under the following four categories-
i. Retail Malls
ii. Shopping Complexes
iii. High-street shops
iv. Retail Warehouses
*refer lotstallmart.com for better clarity

b. The abovementioned properties shall be listed either for ‘Sale’ or ‘rent\lease’ or both

c. Users shall visit the site in case they wish to acquire a retail \ shop space either on ‘sale’ or ‘rent’. These Users would be able to specify the ‘Search Criteria’ through the tool-bars provided on the website – the ‘Search Criteria’ shall comprise of ‘Type of space category’, ‘City’, ‘Locality’, transaction type ie ‘Rent \ Sale’ and ‘Area Range’

d. The main revenue model for the website shall be listing fee ( or advertising charges ) payable by those listing their properties on the website.

Three Main Pages of Website (lotstallmart.com) that need to be designed -
a. Main Home Page (visit the web link - http://lotstallmart.com/ ) - The main home page has the “Search Toolbar” for specifying of Search Criteria by the User. It shall also have the following features & functions-
i. Main Advertising Banner
ii. Featured Projects
iii. New Launches
iv. Toolbar with buttons – ‘Advertise with Us’, ‘Listings Alert’, ‘Mart Wizards’, ‘Advertiser Login’

b. Property Listings Page (visit the web link - http://lotstallmart.com/gurgaon-in-india ) - The List of property options that match the Criteria specified by the ‘User’ get displayed on this page.

c. Property Detail Page - When the ‘User’ clicks on the “More….” Button on the ‘Property Listings Page’ (given in point b. above) the web page with the details of the property opens. (For Example – visit the web link - http://lotstallmart.com/vorne-Shopping-Complex-vorne-quadrion-gurgaon-636 )

Note:- Please refer to attached ‘Shopping’ related images the designer may use them on the website to provide a look & feel of retail if required – either separately or rotate in a single window

Target Market(s)

Retailers & Investors looking for retail space, Real Estate Brokers, Developers

Industry/Entity Type

Advertising

Number of Pages Required

3 page

Requirements
Must have
• Refer to existing site lotstallmart.com -- all the existing functionalities are a must have.
Nice to have
• The Designer may use the retail related images on the website if required for making it more vibrant. Refer attached images Shopping(1-6).jpg

```html
<!DOCTYPE html>
<html lang="en">
<head>
<meta charset="utf-8">
<title>Lotstallmart.com – Home</title>
<link href="https://fonts.googleapis.com/css2?family=Open+Sans:wght@400;600;700&display=swap" rel="stylesheet">
<style>
:root{
  --page:#1f1f1f;
  --panel:#2a2a2a;
  --tab:#333333;
  --footer:#2b2b2b;
  --bottom:#1c1c1c;
  --orange:#f0a030;
  --orange-dark:#e08e1e;
  --white:#ffffff;
  --text-dark:#222222;
  --text-muted:#8a8a8a;
  --text-soft:#b5b5b5;
  --line:#3a3a3a;
}
*{margin:0;padding:0;box-sizing:border-box}
html,body{width:1200px;height:2247px;overflow:hidden}
body{background:var(--page);font-family:"Open Sans",Arial,sans-serif;color:var(--white);position:relative}
.abs{position:absolute}

/* header */
.brand{left:99px;top:48px;display:flex;align-items:center;gap:10px}
.brand-dot{width:26px;height:26px;border-radius:50%;background:var(--orange)}
.brand-name{font-size:27px;font-weight:700;color:var(--white);letter-spacing:-.3px}
.nav{left:471px;top:55px;display:flex;gap:0;font-size:13.5px}
.nav a{color:var(--white);text-decoration:none;margin-right:48px}
.nav a.active{color:var(--orange)}
.login-btn{left:972px;top:50px;width:130px;height:37px;background:var(--orange);color:var(--white);font-size:13.5px;display:flex;align-items:center;justify-content:center}

/* hero */
.hero{left:99px;top:132px;width:1003px;height:540px;background:linear-gradient(120deg,#d9d3c6 0%,#b8a68a 35%,#e0782a 55%,#5a4a3a 80%,#2a2420 100%)}
.dots{left:574px;top:636px;display:flex;gap:6px}
.dots span{width:9px;height:9px;border-radius:50%;background:var(--white)}
.dots span:first-child{background:var(--orange)}

/* search panel */
.search{left:130px;top:170px;width:304px;height:565px;background:var(--white);box-shadow:0 10px 18px rgba(0,0,0,.55);color:var(--text-dark);padding:0 20px}
.search-tag{left:163px;top:159px;width:237px;height:48px;background:var(--orange);color:var(--white);font-size:21px;font-weight:600;display:flex;align-items:center;justify-content:center}
.search-tag::after{content:"";position:absolute;right:-10px;top:0;border-left:10px solid var(--orange-dark);border-bottom:10px solid transparent}
.s-label{position:absolute;left:20px;font-size:11px;color:#555}
.s-label b{font-weight:400;color:var(--orange)}
.formats{position:absolute;left:20px;top:93px;width:264px;height:81px;border:1px solid #ddd;font-size:10.5px;color:#777}
.formats span{position:absolute;display:flex;align-items:center;gap:7px}
.formats i{width:10px;height:10px;border:1px solid #bbb;background:#eee;display:block}
.select{position:absolute;left:20px;width:264px;height:30px;border:1px solid #ccc;font-size:10.5px;color:#aaa;padding:0 8px;display:flex;align-items:center;justify-content:space-between}
.select::after{content:"";border-left:4px solid transparent;border-right:4px solid transparent;border-top:6px solid #888}
.search-btn{position:absolute;left:92px;top:498px;width:120px;height:36px;background:var(--orange);color:var(--white);font-size:17px;font-weight:600;display:flex;align-items:center;justify-content:center}

/* categories */
.cat{top:799px;height:64px;width:229px;background:var(--tab);text-align:center;padding-top:10px}
.cat h3{font-size:16.5px;font-weight:600}
.cat p{font-size:11.5px;margin-top:3px;color:#e6e6e6}
.cat.active{background:var(--orange)}

/* featured */
.featured{left:99px;top:927px;width:1003px;height:440px;background:var(--panel)}
.section-title{font-size:21px;font-weight:600;color:var(--white)}
.arrows{display:flex;gap:4px}
.arrows span{width:17px;height:17px;border-radius:50%;background:var(--white);display:flex;align-items:center;justify-content:center}
.f-card{top:1019px;width:218px;height:316px;background:var(--white);color:var(--text-dark)}
.f-img{width:218px;height:153px}
.f-card h4{font-size:15px;font-weight:600;margin:20px 15px 8px}
.f-card p{font-size:11.5px;line-height:22px;color:#555;margin:0 15px}
.btn{display:inline-flex;align-items:center;justify-content:center;height:34px;padding:0 10px;background:var(--orange);color:var(--white);font-size:12.5px}
.f-card .btn{margin:12px 15px 0}

/* new launches */
.l-card{top:1467px;width:231px}
.l-img{width:231px;height:173px;border:2px solid var(--white)}
.l-card h4{font-size:15px;font-weight:600;color:var(--text-soft);margin-top:23px}
.l-card p{font-size:11.5px;line-height:22px;color:var(--text-muted);margin-top:9px}
.l-card .btn{margin-top:18px;height:34px;padding:0 10px}

/* footer */
.footer{left:0;top:1869px;width:1200px;height:277px;background:var(--footer)}
.f-head{font-size:19px;font-weight:600;color:var(--white)}
.links{font-size:11.5px;color:var(--text-muted);list-style:none;line-height:28.5px}
.links li{display:flex;align-items:center;gap:8px}
.links li::before{content:"";width:7px;height:7px;border-radius:50%;background:var(--orange)}
.divider{width:1px;height:182px;background:var(--line)}
.about{font-size:11.5px;line-height:26px;color:var(--text-muted);width:290px}
.read{font-size:12px;color:var(--orange)}
.address{font-size:11.5px;line-height:26px;color:var(--text-muted)}
.social{display:flex;gap:10px}
.social span{width:26px;height:26px;background:var(--orange)}
.social span:nth-child(2){background:#3b5a9a}
.social span:nth-child(3){background:#3aa0d8}
.bottom{left:0;top:2146px;width:1200px;height:92px;background:var(--bottom)}
.bottom-brand{left:99px;top:2176px;display:flex;align-items:center;gap:8px;font-size:18px;font-weight:700;color:#555}
.bottom-brand i{width:18px;height:18px;border-radius:50%;background:#555;display:block}
.copy{right:99px;top:2181px;font-size:12px;color:#9a9a9a}
.stripe{left:0;top:2238px;width:1200px;height:9px;background:var(--orange)}
</style>
</head>
<body>

<header>
  <div class="abs brand"><span class="brand-dot"></span><span class="brand-name">lotstallmart</span></div>
  <nav class="abs nav">
    <a class="active" href="#">Home</a>
    <a href="#">Advertise With Us</a>
    <a href="#">Mart Wizards</a>
    <a href="#">Listing Alert</a>
  </nav>
  <a class="abs login-btn">Advertiser login</a>
</header>

<section>
  <div class="abs hero" role="img" aria-label="Banner photo: a cheerful shopper holding colourful shopping bags inside a bright mall atrium"></div>
  <div class="abs dots"><span></span><span></span><span></span><span></span></div>

  <form class="abs search">
    <div class="s-label" style="top:58px">Select Retail Format: <b>Meaning of Retail Format</b></div>
    <div class="formats">
      <span style="left:10px;top:18px"><i></i>Retail Malls</span>
      <span style="left:134px;top:18px"><i></i>Shopping Complex</span>
      <span style="left:10px;top:50px"><i></i>High Street Shop</span>
      <span style="left:134px;top:50px"><i></i>Retail Warehouses</span>
    </div>
    <div class="s-label" style="top:190px">Sale Or Rent Or Both</div>
    <div class="select" style="top:218px">Both</div>
    <div class="s-label" style="top:264px">Select City</div>
    <div class="select" style="top:292px">Select</div>
    <div class="s-label" style="top:338px">Select Locality / Micro Market</div>
    <div class="select" style="top:366px">Select</div>
    <div class="s-label" style="top:415px">Enter Keywords</div>
    <div class="select" style="top:443px">Name of Project</div>
    <div class="search-btn">Search</div>
  </form>
  <div class="abs search-tag">Search Property</div>
</section>

<section>
  <div class="abs cat active" style="left:99px"><h3>Retail Malls</h3><p>Centrally Air-Conditioned</p></div>
  <div class="abs cat" style="left:357px"><h3>Shopping Complex</h3><p>Non Air-Conditioned Building</p></div>
  <div class="abs cat" style="left:613px"><h3>High Street Shops</h3><p>Road Facing Retail</p></div>
  <div class="abs cat" style="left:870px"><h3>Retail Warehouses</h3><p>Back-end Ratail Storage</p></div>
</section>

<section>
  <div class="abs featured"></div>
  <h2 class="abs section-title" style="left:124px;top:956px">Featured Projects</h2>
  <div class="abs arrows" style="left:1036px;top:963px">
    <span><svg width="7" height="8"><path d="M5 1L2 4l3 3" stroke="#222" stroke-width="1.6" fill="none"/></svg></span>
    <span><svg width="7" height="8"><path d="M2 1l3 3-3 3" stroke="#222" stroke-width="1.6" fill="none"/></svg></span>
  </div>

  <article class="abs f-card" style="left:124px">
    <div class="f-img" role="img" aria-label="Photo of a hotel tower lit up at dusk" style="background:linear-gradient(#2a3a6a,#6a5a3a 70%,#3a3a2a)"></div>
    <h4>Norva 81 High Street</h4>
    <p>Lorem ipsum dolor sit amet, quo an sonet nullam, id inven.</p>
    <a class="btn">View The Listing</a>
  </article>
  <article class="abs f-card" style="left:369px">
    <div class="f-img" role="img" aria-label="Photo of a golden high-rise tower against a sunset sky" style="background:linear-gradient(#7a6a6a,#c08a4a 60%,#4a3a2a)"></div>
    <h4>Trelin 24K</h4>
    <p>Lorem ipsum dolor sit amet, quo an sonet nullam, id inven.</p>
    <a class="btn">View The Listing</a>
  </article>
  <article class="abs f-card" style="left:614px">
    <div class="f-img" role="img" aria-label="Rendering of a modern commercial building with glass front" style="background:linear-gradient(#cfd8dc,#a8a49a 60%,#6a7a6a)"></div>
    <h4>Vantor</h4>
    <p>Lorem ipsum dolor sit amet, quo an sonet nullam, id inven.</p>
    <a class="btn">View The Listing</a>
  </article>
  <article class="abs f-card" style="left:858px">
    <div class="f-img" role="img" aria-label="Rendering of glass office towers beside a roundabout" style="background:linear-gradient(#9ab0c8,#6a8098 55%,#4a5a4a)"></div>
    <h4>Kestrel One Skyline Center</h4>
    <p>Lorem ipsum dolor sit amet, quo an sonet nullam, id inven.</p>
    <a class="btn">View The Listing</a>
  </article>
</section>

<section>
  <h2 class="abs section-title" style="left:98px;top:1412px">New Launches</h2>
  <div class="abs arrows" style="left:1060px;top:1419px">
    <span><svg width="7" height="8"><path d="M5 1L2 4l3 3" stroke="#222" stroke-width="1.6" fill="none"/></svg></span>
    <span><svg width="7" height="8"><path d="M2 1l3 3-3 3" stroke="#222" stroke-width="1.6" fill="none"/></svg></span>
  </div>

  <article class="abs l-card" style="left:99px">
    <div class="l-img" role="img" aria-label="Photo of a mall entrance plaza with a fountain" style="background:linear-gradient(#8a8ab0,#5a5a6a 60%,#3a3a3a)"></div>
    <h4>The Grand Bazaar Place</h4>
    <p>Cu his sonet tibique, qui ut illud<br>epicurei facilisis, hinc quot .</p>
    <a class="btn">View The Listing</a>
  </article>
  <article class="abs l-card" style="left:356px">
    <div class="l-img" role="img" aria-label="Photo of a mall facade illuminated at night" style="background:linear-gradient(#1a2a4a,#3a4a6a 60%,#5a4a3a)"></div>
    <h4>Riverway Mall</h4>
    <p>Cu his sonet tibique, qui ut illud<br>epicurei facilisis, hinc quot .</p>
    <a class="btn">View The Listing</a>
  </article>
  <article class="abs l-card" style="left:614px">
    <div class="l-img" role="img" aria-label="Photo of escalators inside a mall" style="background:linear-gradient(#4a6a3a,#6a6a5a 50%,#3a3a3a)"></div>
    <h4>Meridia Mall</h4>
    <p>Cu his sonet tibique, qui ut illud<br>epicurei facilisis, hinc quot .</p>
    <a class="btn">View The Listing</a>
  </article>
  <article class="abs l-card" style="left:871px">
    <div class="l-img" role="img" aria-label="Photo of a shopping arcade with lit storefronts at dusk" style="background:linear-gradient(#2a3a5a,#6a4a2a 60%,#3a2a1a)"></div>
    <h4>Solace Mall</h4>
    <p>Cu his sonet tibique, qui ut illud epi-<br>curei facilisis, hinc quot .</p>
    <a class="btn">View The Listing</a>
  </article>
</section>

<footer>
  <div class="abs footer"></div>
  <h3 class="abs f-head" style="left:100px;top:1905px">About Stallpoint Hub</h3>
  <ul class="abs links" style="left:100px;top:1946px">
    <li>About Us</li><li>Privacy Policy</li><li>Terms Of Use</li><li>Contact Us</li>
  </ul>
  <ul class="abs links" style="left:228px;top:1946px">
    <li>Site Map</li><li>Retail Malls</li><li>Shopping Complex</li><li>Retail Warehouses</li>
  </ul>
  <div class="abs divider" style="left:411px;top:1910px"></div>

  <h3 class="abs f-head" style="left:475px;top:1905px">www.lotstallmart.com</h3>
  <p class="abs about" style="left:475px;top:1947px">Lotstallmart.com - About Us<br>Lotstallmart.com is a Specialised Web based platform for Retail Space, featuring properties across India under various formats such as Retail Malls, Shopping Complexes, High-street Shops.</p>
  <a class="abs read" style="left:475px;top:2088px">Read More</a>
  <div class="abs divider" style="left:812px;top:1910px"></div>

  <h3 class="abs f-head" style="left:888px;top:1905px">Contact</h3>
  <svg class="abs" style="left:888px;top:1953px" width="14" height="18" viewBox="0 0 14 18"><path d="M7 0C3.1 0 0 3 0 6.8 0 12 7 18 7 18s7-6 7-11.2C14 3 10.9 0 7 0z" fill="#f0a030"/><circle cx="7" cy="6.8" r="2.6" fill="#2b2b2b"/></svg>
  <p class="abs address" style="left:911px;top:1947px">Stallpoint Hub Unit 208, 2nd Floor,<br>Lorem Ipsum is simply,<br>Sector-y, Gurgaon - 122010</p>
  <div class="abs social" style="left:888px;top:2044px"><span></span><span></span><span></span></div>

  <div class="abs bottom"></div>
  <div class="abs bottom-brand"><i></i>lotstallmart</div>
  <p class="abs copy">Copyright @ 2014 Lotstallmart.com.All Rights Reserved.</p>
  <div class="abs stripe"></div>
</footer>

</body>
</html>
```